Process Serving Company needs a letterhead design

Looking to have a letterhead designed for letters to attorneys advertising our business. We would like something eye catching but professional. Colors and logos are attached. Please add "Process Service and Attorney Support" near the logo or header

Target Market(s)

Attorneys

Font styles to use
Serif
Sans Serif

Colors
33a6d7
0255a3
85cae6
cee9f5
ecf7fb

```html
<!DOCTYPE html>
<html lang="en">
<head>
<meta charset="utf-8">
<title>Mesa Ridge Serve Letterhead</title>
<link href="https://fonts.googleapis.com/css2?family=Source+Sans+3:wght@400;600&family=Arimo:wght@700&display=swap" rel="stylesheet">
<style>
  :root {
    --navy: #0255a3;
    --sky: #33a6d7;
    --paper: #ffffff;
    --backdrop: #e6e6e6;
    --ink: #444444;
    --ink-strong: #4a4a4a;
    --signature-tone: #d9d9d9;
  }
  html, body {
    margin: 0;
    padding: 0;
    width: 1059px;
    height: 1200px;
    overflow: hidden;
    background: var(--backdrop);
  }
  .sheet {
    position: absolute;
    left: 104.5px;
    top: 0;
    width: 924px;
    height: 1305px;
    background: var(--paper);
    transform: scale(0.9195);
    transform-origin: 0 0;
    font-family: "Source Sans 3", sans-serif;
    color: var(--ink);
    overflow: hidden;
  }
  .header-art, .footer-art {
    position: absolute;
    left: 0;
    display: block;
  }
  .header-art { top: 0; }
  .footer-art { top: 1253px; }
  .brand {
    position: absolute;
    left: 82px;
    top: 64px;
    display: flex;
    align-items: center;
    gap: 14px;
  }
  .brand-mark {
    width: 22px;
    height: 22px;
    background: var(--sky);
  }
  .brand-name {
    font-size: 38px;
    font-weight: 600;
    color: var(--sky);
    letter-spacing: 0.5px;
  }
  .contact-list {
    position: absolute;
    left: 697px;
    top: 33px;
    margin: 0;
    padding: 0;
    list-style: none;
    color: #ffffff;
    font-size: 14.5px;
    line-height: 19px;
  }
  .contact-list li {
    display: flex;
    align-items: center;
    gap: 7px;
  }
  .contact-list svg { width: 12px; height: 12px; flex: none; }
  .greeting {
    position: absolute;
    left: 78px;
    top: 301px;
    margin: 0;
    font-family: "Arimo", sans-serif;
    font-weight: 700;
    font-size: 19px;
    color: var(--ink-strong);
  }
  .letter-body {
    position: absolute;
    left: 79px;
    top: 354px;
    width: 774px;
  }
  .letter-body p {
    margin: 0 0 24.2px;
    font-size: 19.2px;
    line-height: 24.2px;
    text-align: justify;
    letter-spacing: 0;
  }
  .signature {
    position: absolute;
    left: 78px;
    top: 924px;
    width: 175px;
    height: 85px;
    background: var(--signature-tone);
  }
  .footer-address {
    position: absolute;
    left: 0;
    top: 1278px;
    width: 924px;
    margin: 0;
    text-align: center;
    color: #ffffff;
    font-size: 13px;
    font-weight: 600;
  }
</style>
</head>
<body>
<main class="sheet">
  <svg class="header-art" width="924" height="140" viewBox="0 0 924 140" aria-hidden="true">
    <path fill="var(--navy)" d="M0 0 H924 V136 H690 C655 136 640 112 626 82 C608 44 596 21 566 21 H0 Z"/>
    <path fill="var(--sky)" d="M0 29 H586 C592 29 596 32 596 32.5 C596 33 592 36 586 36 H0 Z"/>
  </svg>

  <div class="brand">
    <span class="brand-mark"></span>
    <span class="brand-name">Mesa Ridge Serve</span>
  </div>

  <ul class="contact-list">
    <li>
      <svg viewBox="0 0 12 12"><path fill="#fff" d="M1 4 C1 2 3 1 6 1 C9 1 11 2 11 4 L9 5 L8 3.5 H4 L3 5 Z M3 6 H9 L10 10 H2 Z"/></svg>
      <span>480-555-0142</span>
    </li>
    <li>
      <svg viewBox="0 0 12 12"><path fill="#fff" d="M2 5 L3.5 2 H8.5 L10 5 H11 V9 H9.5 V10.5 H8 V9 H4 V10.5 H2.5 V9 H1 V5 Z"/></svg>
      <span>480-555-0187</span>
    </li>
    <li>
      <svg viewBox="0 0 12 12"><path fill="none" stroke="#fff" stroke-width="1.4" d="M1.5 4.5 L6 1.5 L10.5 4.5 V10 H1.5 Z M1.5 4.5 L6 7.5 L10.5 4.5"/></svg>
      <span>info@mesaridgeserve.com</span>
    </li>
    <li>
      <svg viewBox="0 0 12 12"><g fill="none" stroke="#fff" stroke-width="1.1"><circle cx="6" cy="6" r="4.8"/><ellipse cx="6" cy="6" rx="2" ry="4.8"/><path d="M1.2 6 H10.8 M2 3.5 H10 M2 8.5 H10"/></g></svg>
      <span>www.mesaridgeserve.com</span>
    </li>
  </ul>

  <h1 class="greeting">Dear Mr. Harlan,</h1>

  <section class="letter-body">
    <p>Lorem Ipsum is simply dummy text of the printing and typesetting industry. Lorem Ipsum has been the industry's standard dummy text ever since the 1500s, when an unknown printer took a galley of type and scrambled it to make a type specimen book. It has survived not only five centuries, but also the leap into electronic typesetting, remaining essentially unchanged.</p>
    <p>The standard chunk of Lorem Ipsum used since the 1500s is reproduced below for those interested. Sections 1.10.32 and 1.10.33 from "de Rebus Fictis et Veris Verbis" by Tessaro Vell are also reproduced in their exact original form, accompanied by English versions from the 1914 translation by J. Whitcombe</p>
    <p>Lorem Ipsum is simply dummy text of the printing and typesetting industry. Lorem Ipsum has been the industry's standard dummy text ever since the 1500s, when an unknown printer took a galley of type and scrambled it to make a type specimen book. It has survived not only five centuries, but also the leap into electronic typesetting, remaining essentially unchanged. It was popularised in the</p>
    <p>The standard chunk of Lorem Ipsum used since the 1500s is reproduced below for those interested. Sections 1.10.32 and 1.10.33 from "de Rebus Fictis et Veris Verbis" by Tessaro Vell are also reproduced in their exact original form, accompanied by English versions from the 1914 translation by J. Whitcombe</p>
  </section>

  <div class="signature" role="img" aria-label="Handwritten signature of the sender"></div>

  <svg class="footer-art" width="924" height="52" viewBox="0 0 924 52" aria-hidden="true">
    <path fill="var(--navy)" d="M0 0 H33 C33 10 38 18 50 18 H874 C886 18 890 10 890 0 H924 V52 H0 Z"/>
    <rect x="42" y="7" width="840" height="4.5" rx="2.25" fill="var(--sky)"/>
  </svg>
  <p class="footer-address">4120 E Canyon Rd #210 Tempe AZ 85281</p>
</main>
</body>
</html>
```